Animal Eye Clinic needs a Business card

We are a new veterinary ophthalmology practice (Ridgeline Pet Vision Care) and we need a business card designed. We only see animal eyes - we are not a regular veterinary clinic. We already have a logo. We are looking for a professional, good looking business card to hand out to our clients. We are looking for something simple but professional and contemporary. Our logo is likely the only picture/graphic that needs to be on the card.
Updates

Contact Information for Business Card

Delia Vossman, BSc, DVM, MSc, DipACVO
Veterinary Ophthalmologist

Phone: 250.418.3927
Email: ridgelinepetvisioncare@mailbox-example.net
Website: ridgelinepetvisioncare-example.net
Address: 1874 Thornbury Rd
Kelowna, BC, V1X 4M9

Colors

Designer to choose colors to be used in the design.

Requirements
Must have
• Our logo (attached)

```html
<!DOCTYPE html>
<html lang="en">
<head>
<meta charset="utf-8">
<title>Ridgeline Pet Vision Care – Business Card</title>
<link rel="stylesheet" href="https://fonts.googleapis.com/css2?family=Montserrat:wght@600&family=Roboto:wght@400&display=swap">
<style>
  :root {
    --backdrop: #141414;
    --card: #1d1d1e;
    --teal: #1a9bab;
    --grey: #a3a3a3;
    --rule: #555556;
    --icon-fg: #ffffff;
  }
  * { box-sizing: border-box; margin: 0; padding: 0; }
  html, body { width: 1200px; height: 895px; overflow: hidden; background: var(--backdrop); }
  .canvas {
    width: 1200px; height: 895px;
    display: flex; flex-direction: column; align-items: center; justify-content: center; gap: 40px;
  }
  .card {
    position: relative;
    width: 640px; height: 366px;
    background: var(--card);
    box-shadow: 0 10px 24px rgba(0,0,0,.55);
    overflow: hidden;
  }
  .brand {
    display: flex; align-items: center; gap: 14px;
    font-family: "Montserrat", sans-serif; font-weight: 600;
    color: var(--teal); text-transform: uppercase; letter-spacing: .02em;
  }
  .brand-dot { border-radius: 50%; background: var(--teal); flex: none; }

  /* Front */
  .card-front { display: flex; align-items: center; justify-content: center; }
  .card-front .brand { font-size: 27px; }
  .card-front .brand-dot { width: 46px; height: 46px; }

  /* Back */
  .card-back .brand { position: absolute; top: 74px; left: 230px; font-size: 17px; gap: 10px; }
  .card-back .brand-dot { width: 30px; height: 30px; }
  .identity { position: absolute; left: 48px; top: 176px; font-family: "Roboto", sans-serif; }
  .identity-name {
    font-family: "Montserrat", sans-serif; font-weight: 600; font-size: 21px;
    color: var(--teal); text-transform: uppercase; letter-spacing: .02em; margin-bottom: 4px;
  }
  .identity-line { font-size: 13.5px; color: var(--grey); line-height: 1.3; letter-spacing: .02em; }
  .rule { position: absolute; left: 48px; right: 40px; height: 1px; background: var(--rule); }
  .rule-top { top: 252px; }
  .rule-bottom { top: 315px; }
  .contacts {
    position: absolute; left: 48px; right: 40px; top: 262px;
    display: grid; grid-template-columns: auto auto; justify-content: space-between; row-gap: 6px;
    font-family: "Roboto", sans-serif; font-size: 12.5px; color: var(--grey); letter-spacing: .02em;
  }
  .contact { display: flex; align-items: center; gap: 8px; }
  .contact svg { width: 19px; height: 19px; flex: none; }
  .address {
    position: absolute; left: 48px; top: 324px;
    font-family: "Roboto", sans-serif; font-size: 12.5px; color: var(--grey); letter-spacing: .02em;
  }
  .edge-band { position: absolute; left: 0; right: 0; bottom: 0; height: 6px; background: var(--teal); }
</style>
</head>
<body>
<main class="canvas">
  <section class="card card-front" aria-label="Card front">
    <div class="brand"><span class="brand-dot"></span><span>Ridgeline Pet Vision Care</span></div>
  </section>

  <section class="card card-back" aria-label="Card back">
    <div class="brand"><span class="brand-dot"></span><span>Ridgeline Pet Vision Care</span></div>

    <div class="identity">
      <p class="identity-name">Delia Vossman</p>
      <p class="identity-line">BSc, DVM, MSc, DipACVO</p>
      <p class="identity-line">Veterinary Ophthalmologist</p>
    </div>

    <div class="rule rule-top"></div>

    <div class="contacts">
      <div class="contact">
        <svg viewBox="0 0 20 20" aria-hidden="true"><circle cx="10" cy="10" r="10" fill="var(--teal)"/><path d="M7 5.5l1.6 2.3-1 1.1c.6 1.3 1.5 2.2 2.8 2.8l1.1-1 2.3 1.6-.8 1.7c-3.5-.2-6.8-3.5-7-7z" fill="var(--icon-fg)"/></svg>
        <span>250.418.3927</span>
      </div>
      <div class="contact">
        <svg viewBox="0 0 20 20" aria-hidden="true"><circle cx="10" cy="10" r="10" fill="var(--teal)"/><rect x="5" y="6.5" width="10" height="7" rx="1" fill="none" stroke="var(--icon-fg)" stroke-width="1.2"/><path d="M5.4 7l4.6 3.6L14.6 7" fill="none" stroke="var(--icon-fg)" stroke-width="1.2"/></svg>
        <span>ridgelinepetvisioncare@mailbox-example.net</span>
      </div>
      <div class="contact">
        <svg viewBox="0 0 20 20" aria-hidden="true"><circle cx="10" cy="10" r="10" fill="var(--teal)"/><g fill="none" stroke="var(--icon-fg)" stroke-width="1.1"><circle cx="10" cy="10" r="5"/><ellipse cx="10" cy="10" rx="2.2" ry="5"/><path d="M5 10h10M6 7.3h8M6 12.7h8"/></g></svg>
        <span>ridgelinepetvisioncare-example.net</span>
      </div>
    </div>

    <div class="rule rule-bottom"></div>

    <p class="address">1874 Thornbury Rd, Kelowna, BC, V1X 4M9</p>

    <div class="edge-band"></div>
  </section>
</main>
</body>
</html>
```